Computer consultant website

Plimvex Software is a newly started computer consulting company. It's a small one-man company that provides mostly Android applications but also websites in collaboration with designers. I'm running this company on the side of full time university studies.

I'm in need of a website which will function as:
Primarily - I'll direct potential clients to the page so they can read about the company, what i offer and past work.
Secondarily - Making my company visible through the web and maybe getting new clients.

The final design should look modern, clean and professional.

Pages that will be in the final website are (Note that it's not the exact titles as the page will not be in english):
* About
* Services (what Plimvex offers)
* Portfolio/work
* Short news (like ArtHivers "News and press")
* Contact.

Inspiration
http://www.arthiver.example/design/87836
http://www.brookwellstudio.example/
http://www.arthiver.example/design/845881
http://www.arthiver.example/design/1369424 - Lighter design, however a bit cluttered.

No programming code is needed delivered at all. Focus on designing rather then coding.

If you have any questions, do not hesitate to send me a message.

Target Market(s)

Non-technical entrepreneurs and small companies.

Industry/Entity Type

University

Requirements
Must have
• Must have my company logo (see attachment).

Must in any way use both colors from my logo.

A way to logically rearrange content to fit smaller screens. I will implement this design so that it can be pleasantly viewed on mobile devices. You don't necessarily need to provide exactly how the design would look on mobile devices.

I need the following types of page designs:
* Landing page
* Content page
* Portfolio/work (with accompanying inside/clicked) page

Landing/start page must in any way include at least the information:
* Shorter version of "About Plimvex"
* At least 1 most recent portfolio/work entry
* At least 1 most recent news entry
* Services that Plimvex offers.
Nice to have
• -
Should not have
• Testimonials or newsletter.

```html
<!DOCTYPE html>
<html lang="en">
<head>
<meta charset="utf-8">
<title>Plimvex – Works</title>
<link rel="stylesheet" href="https://fonts.googleapis.com/css2?family=Open+Sans:wght@300;400;600&family=PT+Serif&display=swap">
<style>
:root{
  --nav-bg:#353231;
  --blue:#1e7cf2;
  --blue-link:#1a6fe0;
  --ink:#333;
  --page:#f4f4f4;
  --white:#fff;
  --footer:#2b2a2a;
  --footer-text:#ddd;
  --footer-muted:#aaa;
  --card-line:#d8d8d8;
}
*{box-sizing:border-box;margin:0;padding:0}
html,body{width:1200px;height:1053px;overflow:hidden}
body{position:relative;background:var(--page);font-family:"Open Sans",Arial,sans-serif;color:var(--ink)}
a{text-decoration:none;color:inherit}

.main-nav{position:absolute;left:0;top:0;width:1200px;height:52px;background:var(--nav-bg)}
.main-nav a{position:absolute;top:0;height:52px;line-height:52px;color:#fff;font-size:16px;padding:0 15px}
.main-nav a.active{background:var(--blue)}

.site-header{position:absolute;left:0;top:52px;width:1200px;height:116px;background:var(--white);border-bottom:1px solid #e6e6e6}
.brand{position:absolute;left:173px;top:31px;display:flex;align-items:center;gap:14px}
.brand-dot{width:54px;height:54px;border-radius:50%;background:var(--blue)}
.brand-name{font-size:44px;font-weight:600;color:var(--nav-bg);letter-spacing:-1px}
.consult{position:absolute;right:180px;top:36px;display:flex;align-items:center;gap:6px}
.consult-text{text-align:right}
.consult-label{font-size:22px;color:var(--blue);line-height:1.05}
.consult-phone{font-family:"PT Serif",Georgia,serif;font-size:27px;color:#666;line-height:1.05}

.page-title{position:absolute;left:181px;top:192px;font-size:34px;font-weight:300;color:#222}
.title-rule{position:absolute;left:182px;top:240px;width:834px;height:1px;background:#ddd}
.filters{position:absolute;left:185px;top:259px;font-size:13px;color:#888;display:flex;gap:9px}
.filters .sep{color:#bbb}
.filters .active{color:var(--blue)}

.work-card{position:absolute;width:258px;height:184px;background:var(--white);border:1px solid var(--card-line);box-shadow:0 1px 2px rgba(0,0,0,.06);overflow:hidden}
.work-thumb{position:absolute;left:7px;top:7px;width:243px;height:125px}
.work-title{position:absolute;left:7px;top:141px;font-size:12.5px;color:var(--blue-link)}
.work-type{position:absolute;left:7px;top:157px;font-size:12.5px;color:#555}
.zoom{position:absolute;right:0;bottom:0}

.cta{position:absolute;left:183px;top:749px;width:829px;height:111px;border:1px solid #cfe0fb;background:linear-gradient(#d4e5fd,#6aa5f8);box-shadow:0 1px 3px rgba(0,0,0,.1)}
.cta-heading{position:absolute;right:286px;top:20px;font-size:35px;font-weight:300;color:var(--blue);white-space:nowrap;line-height:1}
.cta-sub{position:absolute;right:286px;top:52px;font-size:26px;color:#222;line-height:1.1}
.cta-button{position:absolute;left:588px;top:27px;width:184px;height:54px;border:1px solid #999;background:linear-gradient(#f8f8f8,#d6d6d6);font-size:22px;font-weight:600;color:#444;text-align:center;line-height:52px}

.site-footer{position:absolute;left:0;top:916px;width:1200px;height:137px;background:var(--footer)}
.footer-nav{position:absolute;left:188px;top:41px;display:flex;gap:25px;font-size:13px;color:var(--footer-text)}
.copyright{position:absolute;left:188px;top:73px;font-size:13px;color:var(--footer-muted)}
.touch{position:absolute;left:795px;top:27px;width:180px;text-align:center;font-size:12.5px;color:var(--footer-text)}
.touch::before,.touch::after{content:"";position:absolute;top:9px;width:30px;height:1px;background:#555}
.touch::before{left:0}.touch::after{right:0}
.socials{position:absolute;left:780px;top:50px;display:flex;gap:5px}
.socials span{width:35px;height:35px;border-radius:50%;background:#8a8a8a}
.call{position:absolute;left:812px;top:97px;font-size:12.5px;color:#6aa8ff}
</style>
</head>
<body>

<nav class="main-nav">
  <a style="left:174px">Home</a>
  <a style="left:250px">About</a>
  <a style="left:330px">Services</a>
  <a class="active" style="left:421px;width:74px;text-align:center">Works</a>
  <a style="left:498px">News</a>
  <a style="left:569px">Contact</a>
</nav>

<header class="site-header">
  <div class="brand"><span class="brand-dot"></span><span class="brand-name">Plimvex</span></div>
  <div class="consult">
    <svg class="phone-icon" width="18" height="42" viewBox="0 0 18 42" aria-hidden="true">
      <rect x="1" y="1" width="16" height="40" rx="2" fill="none" stroke="#666" stroke-width="2"/>
      <rect x="4" y="5" width="10" height="12" fill="#666"/>
      <g fill="#666"><rect x="4" y="21" width="3" height="3"/><rect x="8" y="21" width="3" height="3"/><rect x="12" y="21" width="3" height="3"/><rect x="4" y="26" width="3" height="3"/><rect x="8" y="26" width="3" height="3"/><rect x="12" y="26" width="3" height="3"/><rect x="4" y="31" width="3" height="3"/><rect x="8" y="31" width="3" height="3"/><rect x="12" y="31" width="3" height="3"/></g>
    </svg>
    <div class="consult-text">
      <div class="consult-label">Free Consultancy</div>
      <div class="consult-phone">010 555 0147</div>
    </div>
  </div>
</header>

<h1 class="page-title">Works</h1>
<div class="title-rule"></div>
<div class="filters">
  <span class="active">All</span><span class="sep">|</span><span>Android App</span><span class="sep">|</span><span>Website Design</span><span class="sep">|</span><span>SEO</span><span class="sep">|</span><span>User Experience Design</span>
</div>

<svg width="0" height="0" style="position:absolute">
  <symbol id="zoom-corner" viewBox="0 0 38 38">
    <path d="M38 0 L38 38 L0 38 Z" fill="#dcdcdc"/>
    <path d="M38 0 L0 38 L0 36 L36 0 Z" fill="#fff"/>
    <circle cx="25" cy="25" r="4.5" fill="none" stroke="#555" stroke-width="1.5"/>
    <line x1="28" y1="28" x2="32" y2="32" stroke="#555" stroke-width="2"/>
    <line x1="23" y1="25" x2="27" y2="25" stroke="#555" stroke-width="1.2"/>
    <line x1="25" y1="23" x2="25" y2="27" stroke="#555" stroke-width="1.2"/>
  </symbol>
</svg>

<article class="work-card" style="left:183px;top:298px">
  <div class="work-thumb" role="img" aria-label="Website screenshot: woman in a red field with coaching programme banner" style="background:linear-gradient(135deg,#3a2b2b,#d8304a 45%,#3bb8d8)"></div>
  <a class="work-title">Meetwell Coaching</a><div class="work-type">Website Design and Development</div>
  <svg class="zoom" width="38" height="38"><use href="#zoom-corner"/></svg>
</article>
<article class="work-card" style="left:470px;top:298px">
  <div class="work-thumb" role="img" aria-label="Website screenshot: construction worker in safety gear" style="background:linear-gradient(#5d7a4a,#8a9a70 45%,#c9c4b8 85%,#e4e4e4)"></div>
  <a class="work-title">Terravolt</a><div class="work-type">Search Engine Optimization</div>
  <svg class="zoom" width="38" height="38"><use href="#zoom-corner"/></svg>
</article>
<article class="work-card" style="left:756px;top:298px">
  <div class="work-thumb" role="img" aria-label="Game website screenshot: cartoon beach with sign-up panels" style="background:linear-gradient(#d8eef9,#9fd2ee 45%,#c8e4c0 70%,#f3e6a8)"></div>
  <a class="work-title">Hopscamper</a><div class="work-type">Android Application</div>
  <svg class="zoom" width="38" height="38"><use href="#zoom-corner"/></svg>
</article>

<article class="work-card" style="left:183px;top:517px">
  <div class="work-thumb" role="img" aria-label="Website screenshot: engineers in hard hats on site" style="background:linear-gradient(#3a3632,#9a8a6a 30%,#b39a6a 65%,#d8b040 85%,#e8e2d4)"></div>
  <a class="work-title">Terravolt</a><div class="work-type">Android and iOS Application</div>
  <svg class="zoom" width="38" height="38"><use href="#zoom-corner"/></svg>
</article>
<article class="work-card" style="left:470px;top:517px">
  <div class="work-thumb" role="img" aria-label="Game website screenshot: cartoon meadow with login forms" style="background:linear-gradient(#3cc0e8,#8fd8f0 40%,#bfe3f3 60%,#8cc63f)"></div>
  <a class="work-title">Hopscamper</a><div class="work-type">Website Design and Development</div>
  <svg class="zoom" width="38" height="38"><use href="#zoom-corner"/></svg>
</article>
<article class="work-card" style="left:756px;top:517px">
  <div class="work-thumb" role="img" aria-label="Website screenshot: black and white photo of woman in a field" style="background:linear-gradient(135deg,#3a3a3a,#9a9a9a 50%,#5a5a5a)"></div>
  <a class="work-title">Meetwell Coaching</a><div class="work-type">Android and iOS Application</div>
  <svg class="zoom" width="38" height="38"><use href="#zoom-corner"/></svg>
</article>

<section class="cta">
  <h2 class="cta-heading">Let's Discuss Your Project with us</h2>
  <p class="cta-sub">What do you need?</p>
  <a class="cta-button">CONTACT US</a>
</section>

<footer class="site-footer">
  <nav class="footer-nav"><a>Home</a><a>About</a><a>Services</a><a>Works</a><a>News</a><a>Contact</a></nav>
  <p class="copyright">Copyright © 2013 Plimvex. All rights reserved | Terms and Conditions | Privacy Policy</p>
  <div class="touch">KEEP IN TOUCH</div>
  <div class="socials"><span></span><span></span><span></span><span></span><span></span></div>
  <p class="call">Call us at &nbsp;010 555 0147</p>
</footer>

</body>
</html>
```